Facebook Header Design Project.

I'm supplying white and colored logos. The Facebook page already exists. URL = https://www.brindlepost.example/quillarc.studio The design should not be based on what's already there. Consider mobile implications of the design. This Design will form the designs of other social media headers. QuillArc is a web design | digital marketing company.

Target Market(s)

People interested in web design | digital marketing services.

Industry/Entity Type

QuillArc is a web design | digital marketing company. That should be clear in the design.

Colors
0054AA
0677BA
7BADD7
CADEEF
E8F1F8

Requirements
Must have
• Logo. Use Facebook header image dimension.
Nice to have
• Use a color scheme like the logo and feel free to add a color or two from the other side of the color whee.

```html
<!DOCTYPE html>
<html lang="en">
<head>
<meta charset="utf-8">
<title>QuillArc — Cover Header</title>
<link rel="stylesheet" href="https://fonts.googleapis.com/css2?family=Nunito:wght@400;600;700;800&display=swap">
<style>
  :root {
    --brand-deep: #0054AA;
    --brand-mid: #0677BA;
    --brand-sky: #7BADD7;
    --brand-mist: #CADEEF;
    --brand-ice: #E8F1F8;
    --white: #FFFFFF;
    --frame: #3E3D4A;
    --page-blue: #1877F2;
    --page-blue-soft: #E7F3FF;
    --ink: #050505;
    --ink-muted: #65676B;
    --chip: #E4E6EB;
    --rule: #CED0D4;
    --backdrop-top: #5467BE;
  }
  * { margin: 0; padding: 0; box-sizing: border-box; }
  html, body {
    width: 1200px;
    height: 853px;
    overflow: hidden;
    background: var(--white);
    font-family: "Nunito", sans-serif;
  }
  .canvas { position: relative; width: 1200px; height: 853px; }

  /* ---------- page preview panel ---------- */
  .preview {
    position: absolute;
    left: 49px; top: 42px;
    width: 1102px; height: 493px;
    background: var(--frame);
    border-radius: 20px;
  }
  .preview__screen {
    position: absolute;
    left: 18px; top: 17px;
    width: 1066px; height: 458px;
    overflow: hidden;
    background: linear-gradient(180deg, var(--backdrop-top) 0%, #B9C3E6 40%, var(--white) 60%, var(--white) 100%);
  }
  .preview__screen::after {
    content: "";
    position: absolute;
    left: 0; right: 0; bottom: 0;
    height: 9px;
    background: #F0F2F5;
    border-top: 1px solid #DADDE1;
  }
  .preview__page {
    position: absolute;
    left: 0; top: 289px;
    width: 100%; height: 160px;
    background: var(--white);
  }
  .preview .cover { left: 150px; top: 0; }

  /* ---------- cover (shared) ---------- */
  .cover {
    position: absolute;
    width: 767px; height: 289px;
    background: var(--brand-deep);
    overflow: hidden;
    color: var(--white);
  }
  .cover__wordmark {
    position: absolute;
    top: 44px; left: 0; width: 100%;
    text-align: center;
    font-weight: 800;
    font-size: 56px;
    line-height: 1;
  }
  .cover__tagline {
    position: absolute;
    top: 122px; left: 0; width: 100%;
    text-align: center;
    font-weight: 400;
    font-size: 13.5px;
  }
  .cover__hill { position: absolute; left: 0; top: 0; width: 767px; height: 289px; }
  .cover__devices {
    position: absolute;
    left: 246px; top: 181px;
    width: 274px; height: 108px;
    border-radius: 10px 10px 0 0;
    background: linear-gradient(180deg, var(--brand-sky) 0%, var(--brand-ice) 45%, var(--brand-mist) 100%);
  }
  .cover--standalone {
    left: 280px; top: 566px;
    transform: scale(0.8344);
    transform-origin: 0 0;
  }

  /* ---------- profile block ---------- */
  .profile__avatar {
    position: absolute;
    left: 235px; top: 318px;
    width: 106px; height: 106px;
    border-radius: 50%;
    background: var(--white);
    border: 3px solid var(--page-blue);
    display: flex; align-items: center; justify-content: center;
    font-weight: 800; font-size: 17px;
    color: var(--brand-deep);
  }
  .profile__name {
    position: absolute;
    left: 362px; top: 353px;
    font-weight: 800; font-size: 22px;
    color: var(--ink);
  }
  .profile__meta {
    position: absolute;
    left: 363px; top: 384px;
    font-size: 13.5px;
    color: var(--ink-muted);
  }
  .profile__call {
    position: absolute;
    left: 686px; top: 386px;
    width: 254px; height: 32px;
    border-radius: 5px;
    background: var(--page-blue);
    color: var(--white);
    font-weight: 700; font-size: 14px;
    display: flex; align-items: center; justify-content: center; gap: 6px;
  }
  .profile__rule {
    position: absolute;
    left: 226px; top: 441px;
    width: 714px; height: 1px;
    background: var(--rule);
  }

  /* ---------- tabs & actions ---------- */
  .tabs {
    position: absolute;
    left: 226px; top: 442px;
    display: flex; list-style: none;
    font-size: 12.5px; font-weight: 600;
    color: var(--ink-muted);
  }
  .tabs__item { padding: 14px 13px 11px; line-height: 1; }
  .tabs__item--active { color: var(--page-blue); border-bottom: 3px solid var(--page-blue); }
  .tabs__caret { font-size: 8px; margin-left: 4px; vertical-align: 1px; }

  .actions {
    position: absolute;
    top: 452px; left: 651px;
    display: flex; gap: 7px;
  }
  .actions__btn {
    height: 29px;
    border-radius: 5px;
    background: var(--chip);
    color: var(--ink);
    font-size: 12.5px; font-weight: 600;
    display: flex; align-items: center; justify-content: center; gap: 5px;
  }
  .actions__btn--like { width: 105px; background: var(--page-blue-soft); color: var(--page-blue); }
  .actions__btn--message { width: 87px; }
  .actions__btn--icon { width: 38px; }
  .actions__dot { width: 11px; height: 11px; border-radius: 50%; background: currentColor; }

  .edit-badge {
    position: absolute;
    left: 1037px; top: 454px;
    width: 38px; height: 38px;
    border-radius: 50%;
    background: var(--white);
    box-shadow: 0 2px 6px rgba(0,0,0,0.25);
    display: flex; align-items: center; justify-content: center;
  }
</style>
</head>
<body>
  <main class="canvas">
    <div class="preview">
      <div class="preview__screen">
        <div class="preview__page"></div>

        <section class="cover">
          <h1 class="cover__wordmark">QuillArc</h1>
          <p class="cover__tagline">Web Design &amp; Digital Marketing Services</p>
          <svg class="cover__hill" viewBox="0 0 767 289" aria-hidden="true">
            <path d="M141 289 Q383 258 624 289 Z" fill="#FFFFFF"/>
          </svg>
          <div class="cover__devices" role="img" aria-label="Illustration of a desktop monitor, tablet and phone showing web page layouts with a cursor"></div>
        </section>

        <div class="profile__avatar">QuillArc</div>
        <h2 class="profile__name">QuillArc</h2>
        <p class="profile__meta">@quillarc.studio · Digital Creator</p>
        <div class="profile__call">
          <svg width="14" height="14" viewBox="0 0 24 24" aria-hidden="true"><path fill="#FFFFFF" d="M6.6 10.8a15.1 15.1 0 0 0 6.6 6.6l2.2-2.2a1 1 0 0 1 1-.25 11.4 11.4 0 0 0 3.6.57 1 1 0 0 1 1 1V20a1 1 0 0 1-1 1A17 17 0 0 1 3 4a1 1 0 0 1 1-1h3.5a1 1 0 0 1 1 1c0 1.25.2 2.45.57 3.57a1 1 0 0 1-.25 1z"/></svg>
          Call Now
        </div>
        <div class="profile__rule"></div>

        <ul class="tabs">
          <li class="tabs__item tabs__item--active">Home</li>
          <li class="tabs__item">Offers</li>
          <li class="tabs__item">Photos</li>
          <li class="tabs__item">Videos</li>
          <li class="tabs__item">More<span class="tabs__caret">▼</span></li>
        </ul>

        <div class="actions">
          <div class="actions__btn actions__btn--like"><span class="actions__dot"></span>Like</div>
          <div class="actions__btn actions__btn--message"><span class="actions__dot"></span>Message</div>
          <div class="actions__btn actions__btn--icon">
            <svg width="15" height="15" viewBox="0 0 24 24" aria-hidden="true"><circle cx="10" cy="10" r="7" fill="none" stroke="#050505" stroke-width="2.4"/><path d="M15 15l6 6" stroke="#050505" stroke-width="2.4" stroke-linecap="round"/></svg>
          </div>
          <div class="actions__btn actions__btn--icon">
            <svg width="14" height="4" viewBox="0 0 14 4" aria-hidden="true"><circle cx="2" cy="2" r="1.6" fill="#050505"/><circle cx="7" cy="2" r="1.6" fill="#050505"/><circle cx="12" cy="2" r="1.6" fill="#050505"/></svg>
          </div>
        </div>

        <div class="edit-badge">
          <svg width="18" height="18" viewBox="0 0 24 24" aria-hidden="true"><path d="M11 4H5a1 1 0 0 0-1 1v14a1 1 0 0 0 1 1h14a1 1 0 0 0 1-1v-6" fill="none" stroke="#050505" stroke-width="2.2" stroke-linecap="round"/><path d="M18 3l3 3-9 9H9v-3z" fill="none" stroke="#050505" stroke-width="2.2" stroke-linejoin="round"/></svg>
        </div>
      </div>
    </div>

    <section class="cover cover--standalone">
      <h2 class="cover__wordmark">QuillArc</h2>
      <p class="cover__tagline">Web Design &amp; Digital Marketing Services</p>
      <svg class="cover__hill" viewBox="0 0 767 289" aria-hidden="true">
        <path d="M141 289 Q383 258 624 289 Z" fill="#FFFFFF"/>
      </svg>
      <div class="cover__devices" role="img" aria-label="Illustration of a desktop monitor, tablet and phone showing web page layouts with a cursor"></div>
    </section>
  </main>
</body>
</html>
```